Power Point Template

I would like to have a power point template for our company.
See our website: www.brekkavikfjord.se for logo/colors and inspiration.

The template will be used for bank meetings etc, so it should be formal and professional.

Should show examples of various layouts.
Updates

I want the following headings/sections/example slides: - Slide with table of contents - Slide with bullets (just to show how a bullet list looks like) - Slide with project timeline - Slide with business case calculations (table e.g.) - slide with pictures with room for descriptive text (to show inspirational pictures, one slide per section: exterior, interior upper floor, exterior lower floor)? - Slide where our buildings are described (bullet list) - Slide with presentation of our business partners - First page with a faded background picture of our building (the one where our logo is shown)

Industry/Entity Type

It Company

```html
<!DOCTYPE html>
<html lang="en">
<head>
<meta charset="UTF-8">
<title>Company Overview</title>
<link href="https://fonts.googleapis.com/css2?family=Roboto+Condensed:wght@300;400;700&display=swap" rel="stylesheet">
<style>
  :root {
    --page: #f7f7f7;
    --ink: #1f1f1f;
    --body: #3a3a3a;
    --navy: #1c2b45;
    --blue: #1f5fae;
    --yellow: #fbb034;
    --charcoal: #343434;
    --ring: #c9c9c9;
    --footer: #8a97a3;
    --white: #ffffff;
  }
  * { margin: 0; padding: 0; box-sizing: border-box; }
  html, body { width: 1200px; height: 900px; overflow: hidden; background: var(--page); }
  .slide {
    position: relative; width: 1200px; height: 900px; overflow: hidden;
    background: var(--page);
    font-family: "Roboto Condensed", "Arial Narrow", sans-serif; color: var(--body);
  }
  .slide-title {
    position: absolute; top: 66px; left: 0; width: 1175px; text-align: center;
    font-size: 40px; font-weight: 400; color: var(--ink); letter-spacing: 0.5px;
  }
  .slide-title strong { font-weight: 700; margin-left: 10px; }
  .title-rule { position: absolute; top: 122px; height: 4px; }
  .title-rule.accent { left: 315px; width: 245px; background: var(--yellow); }
  .title-rule.primary { left: 560px; width: 322px; background: var(--blue); }

  .brand {
    position: absolute; top: 40px; right: 22px;
    display: flex; align-items: center; gap: 8px;
    font-size: 20px; font-weight: 700; color: var(--navy);
  }
  .brand-square { width: 16px; height: 16px; background: var(--navy); }

  .circle { position: absolute; border-radius: 50%; }
  .photo-main {
    left: 238px; top: 205px; width: 280px; height: 280px;
    border: 1.5px solid #9a9a9a;
    background: linear-gradient(160deg, #a9c3de 0%, #8aa7c6 30%, #2b3542 55%, #1c2430 80%, #5b6470 100%);
  }
  .photo-small {
    border: 4px solid var(--blue); outline: 3px solid var(--white); outline-offset: -7px;
  }
  .photo-left {
    left: 53px; top: 520px; width: 150px; height: 150px;
    background: linear-gradient(180deg, #b8c9d6 0%, #9aa8b3 45%, #6f7a80 75%, #4b5540 100%);
  }
  .photo-middle {
    left: 216px; top: 480px; width: 138px; height: 138px;
    background: linear-gradient(135deg, #d4d9de 0%, #aeb5bc 50%, #7f8891 100%);
  }
  .photo-right {
    left: 327px; top: 567px; width: 180px; height: 180px;
    background: linear-gradient(180deg, #b8c9d6 0%, #9aa8b3 45%, #6f7a80 75%, #4b5540 100%);
  }

  .badge {
    display: flex; align-items: center; justify-content: center;
    background: var(--ring);
  }
  .badge-inner {
    border-radius: 50%; display: flex; flex-direction: column;
    align-items: center; justify-content: center; text-align: center; color: var(--white);
  }
  .badge-title { font-size: 24px; font-weight: 700; margin-bottom: 2px; }
  .badge-text { font-size: 16px; font-weight: 700; line-height: 1.42; }
  .badge-accent { left: 51px; top: 280px; width: 214px; height: 214px; }
  .badge-accent .badge-inner { width: 190px; height: 190px; background: var(--yellow); padding: 0 36px; }
  .badge-dark { left: 429px; top: 399px; width: 186px; height: 186px; }
  .badge-dark .badge-inner { width: 164px; height: 164px; background: var(--charcoal); padding: 0 18px; }
  .badge-dark .badge-title { font-size: 22px; }
  .badge-dark .badge-text { font-size: 14.5px; }

  .overview-copy { position: absolute; left: 702px; top: 228px; width: 470px; }
  .overview-subtext { font-size: 25px; font-weight: 400; color: #333; margin-bottom: 4px; }
  .overview-copy p { font-size: 22px; font-weight: 400; line-height: 33px; color: var(--body); margin-bottom: 6px; }

  .footer-band { position: absolute; left: 0; bottom: 0; width: 1200px; height: 27px; background: var(--footer); }
</style>
</head>
<body>
<main class="slide">
  <h1 class="slide-title">COMPANY<strong>OVERVIEW</strong></h1>
  <div class="title-rule accent"></div>
  <div class="title-rule primary"></div>

  <div class="brand"><span class="brand-square"></span>Company Name</div>

  <div class="circle photo-main" role="img" aria-label="Photo of a dark clad office building against a blue sky"></div>
  <div class="circle photo-small photo-left" role="img" aria-label="Photo of the building front with trees and parked cars"></div>
  <div class="circle photo-small photo-middle" role="img" aria-label="Photo of a grey building corner with company signage"></div>
  <div class="circle photo-small photo-right" role="img" aria-label="Photo of the building front with trees and parked cars"></div>

  <div class="circle badge badge-accent">
    <div class="badge-inner">
      <div class="badge-title">Title Here</div>
      <div class="badge-text">Lorem Ipsum is simply dummy text of the printing and typesetting industry.</div>
    </div>
  </div>
  <div class="circle badge badge-dark">
    <div class="badge-inner">
      <div class="badge-title">Title Here</div>
      <div class="badge-text">Lorem Ipsum is simply dummy text of the printing and typesetting industry.</div>
    </div>
  </div>

  <section class="overview-copy">
    <h2 class="overview-subtext">Subtext here</h2>
    <p>Lorem Ipsum is simply dummy text of the printing and typesetting industry. Lorem Ipsum has been the industry's standard dummy text ever since the 1500s, when an unknown printer took a galley of type and scrambled it to make a type specimen book. It has survived not only five centuries, but also the leap into electronic typesetting.</p>
    <p>Lorem Ipsum is simply dummy text of the printing and typesetting industry. Lorem Ipsum has been the industry's standard dummy text ever since the 1500s, when an unknown printer took a galley of type and scrambled it to make a type specimen book. It has survived not only five centuries, but also the leap into electronic typesetting.</p>
  </section>

  <div class="footer-band"></div>
</main>
</body>
</html>
```